Business card for a Exhibition booth fabrication company

Hi. My company would like to change our corporate name card. We are an events and Exhibition stand builder company. We would like our corporate name card to resonate what we do. I need someone to create something unique that relates to the industry that I am in. The graphic designer should be creative to incorporate the elements of my industry and try to blend in well in the design of the card. Our aim is to ensure that we are unique and our card can look different from our competitors.
Updates

Target Market(s)

Marketing and events manager from all companies

Contact Information for Business Card

The business card should have the following details:
Name
Job Title
Email
Website

Colors

Designer to choose colors to be used in the design.

Requirements
Must have
• The card must be look something that is relevant to the service that I am providing. My website is: www.velmora-buildworks.com
• You can see my website to get more information on what service that I am doing
Nice to have
• On the back of my card, I would like to have a globe image with the incorporation of my company logo. This is to indicate that my services can be done in any part of the world.

```html
<!DOCTYPE html>
<html lang="en">
<head>
<meta charset="utf-8">
<title>Velmora Buildworks – Business Card</title>
<link rel="stylesheet" href="https://fonts.googleapis.com/css2?family=Open+Sans:wght@400;600;700&family=Montserrat:wght@500;600&display=swap">
<style>
  :root {
    --brand-red: #ed1c24;
    --map-red: #f04a50;
    --ink-gray: #5b5b5d;
    --band-gray: #6d6e71;
    --rule-gray: #b9b9b9;
    --card-white: #ffffff;
    --silver: #dcdcdc;
    --bg-light: #d8d9db;
    --bg-dark: #a3a4a7;
  }
  * { margin: 0; padding: 0; box-sizing: border-box; }
  html, body { width: 1200px; height: 1118px; overflow: hidden; }
  body {
    background: linear-gradient(90deg, var(--bg-light), var(--bg-dark));
    position: relative;
    font-family: "Open Sans", Arial, sans-serif;
  }
  .card {
    position: absolute;
    left: 223px;
    width: 754px;
    height: 430px;
    border-radius: 24px;
    overflow: hidden;
    box-shadow: 0 2px 6px rgba(0,0,0,0.12);
  }
  .card-front { top: 100px; background: var(--card-white); }
  .card-back { top: 590px; background: var(--brand-red); }

  .front-brand {
    position: absolute;
    left: 30px; top: 150px;
    width: 340px;
    text-align: center;
  }
  .brand-mark {
    display: block;
    width: 58px; height: 58px;
    margin: 0 auto 22px;
    border-radius: 50%;
    background: var(--brand-red);
  }
  .brand-name {
    font-family: "Montserrat", Arial, sans-serif;
    font-weight: 600;
    font-size: 21px;
    letter-spacing: 1.5px;
    color: var(--ink-gray);
    white-space: nowrap;
  }
  .divider {
    position: absolute;
    left: 404px; top: 97px;
    width: 2px; height: 168px;
    background: var(--rule-gray);
  }
  .contact {
    position: absolute;
    left: 423px; top: 92px;
    color: var(--ink-gray);
    font-size: 18.5px;
    line-height: 1.2;
  }
  .address p { margin-bottom: 8px; }
  .contact-list { list-style: none; margin-top: 14px; }
  .contact-list li { display: flex; align-items: center; gap: 9px; margin-bottom: 11px; }
  .contact-list svg { width: 20px; height: 20px; flex: none; }

  .wave { position: absolute; left: 0; top: 0; width: 754px; height: 430px; }
  .holder {
    position: absolute;
    left: 480px; top: 352px;
    width: 250px;
    text-align: center;
    color: var(--card-white);
  }
  .holder-name { font-family: "Open Sans", Arial, sans-serif; font-weight: 700; font-size: 24px; letter-spacing: 0.3px; }
  .holder-title { font-size: 18px; letter-spacing: 0.8px; margin-top: 2px; }

  .world-map {
    position: absolute;
    left: 0; top: 69px;
    width: 754px; height: 264px;
    background: radial-gradient(ellipse at 50% 50%, rgba(255,255,255,0.16), rgba(255,255,255,0.06) 70%, rgba(255,255,255,0) 100%);
  }
  .back-brand {
    position: absolute;
    left: 0; top: 150px;
    width: 754px;
    text-align: center;
  }
  .back-mark {
    display: block;
    width: 90px; height: 90px;
    margin: 0 auto 22px;
    border-radius: 50%;
    background: var(--silver);
  }
  .back-name {
    font-family: "Montserrat", Arial, sans-serif;
    font-weight: 600;
    font-size: 30px;
    letter-spacing: 3px;
    color: var(--silver);
  }
  .back-web {
    position: absolute;
    left: 0; top: 388px;
    width: 754px;
    text-align: center;
    color: var(--card-white);
    font-size: 20px;
    letter-spacing: 3.5px;
  }
</style>
</head>
<body>
  <section class="card card-front">
    <div class="front-brand">
      <span class="brand-mark"></span>
      <div class="brand-name">VELMORA BUILDWORKS</div>
    </div>
    <div class="divider"></div>
    <div class="contact">
      <div class="address">
        <p>Street Name, City Name</p>
        <p>Zipcode - 01234</p>
      </div>
      <ul class="contact-list">
        <li>
          <svg viewBox="0 0 20 20"><path d="M5 2 L8 6 L6.5 8 C7.5 10.5 9.5 12.5 12 13.5 L14 12 L18 15 L16 18 C9 18 2 11 2 4 Z" fill="var(--brand-red)"/></svg>
          012-345-6789
        </li>
        <li>
          <svg viewBox="0 0 20 20"><rect x="2" y="4" width="16" height="12" fill="var(--brand-red)"/><path d="M2 4 L10 11 L18 4" stroke="#fff" stroke-width="1.5" fill="none"/></svg>
          info@velmora-buildworks.com
        </li>
        <li>
          <svg viewBox="0 0 20 20" fill="none" stroke="var(--brand-red)" stroke-width="1.6"><circle cx="10" cy="10" r="8"/><ellipse cx="10" cy="10" rx="3.5" ry="8"/><path d="M2 10 H18 M3.5 6 H16.5 M3.5 14 H16.5"/></svg>
          www.velmora-buildworks.com
        </li>
      </ul>
    </div>
    <svg class="wave" viewBox="0 0 754 430">
      <path d="M0 360 C250 330 500 296 754 318 L754 430 L0 430 Z" fill="var(--brand-red)"/>
      <path d="M0 372 C250 342 500 312 754 331 L754 430 L0 430 Z" fill="var(--card-white)"/>
      <path d="M0 380 C250 352 500 325 754 338 L754 430 L0 430 Z" fill="var(--brand-red)"/>
      <path d="M0 392 C150 380 320 362 500 344 C330 372 170 400 80 430 L0 430 Z" fill="var(--band-gray)"/>
      <path d="M0 392 C150 380 320 362 500 344" stroke="var(--card-white)" stroke-width="4" fill="none"/>
    </svg>
    <div class="holder">
      <div class="holder-name">DANIEL HARROW</div>
      <div class="holder-title">PRESIDENT</div>
    </div>
  </section>

  <section class="card card-back">
    <div class="world-map" role="img" aria-label="Faint world map spanning the card"></div>
    <div class="back-brand">
      <span class="back-mark"></span>
      <div class="back-name">VELMORA BUILDWORKS</div>
    </div>
    <div class="back-web">www.velmora-buildworks.com</div>
  </section>
</body>
</html>
```